Kestrel Baseball & Softball Camp 2017

Design a flyer that will promote our 2017 summer camp for boys and girls softball.

Weeks of
July 10th - 14th
July 17th - 21st.

Players ages 5 - 11.
Full day = 9:30am - 2:30pm half day = 9:30am - 11:30am.
$295 / full day : $195/ half day

Hosted by "Kestrel Baseball" affiliated with the Harbor Comets Travel Baseball & Softball Club and the Maple Ridge Youth League,

Camp Location MRYL, Route 9C Birch Hollow.

PHone 555-240-7813, email info@kestrelball.example

The color should be "Red white and blue color scheme" with dates and location standing out. Kestrel Logo should be prominent MRYL and Comets smaller and secondary.

Feel free to use stock photo's if available. visit www.harborcomets.example for more pictures and there are links for the 2017 summer camp there with possibly some more information.

Target Market(s)

to catch the eye of parents of players ages 5 - 11 already at little league or shopping in local stores

Colors
ec1f27
0355a3
ffffff

Requirements
Must have
• red white and blue design,
• Kestrel logo and summer camp prominent so it catches the eye and explains what it is right away.
• the comets and maple ridge logo's a the bottom showing the affiliation.
Nice to have
• stock photo's or something showing players having a great time or a beautiful ballpark
Should not have
• to much clutter or hard to figure out what it's for

```html
<!DOCTYPE html>
<html lang="en">
<head>
<meta charset="utf-8">
<title>Kestrel Softball Summer Camp 2017</title>
<link href="https://fonts.googleapis.com/css2?family=Bebas+Neue&family=Kaushan+Script&family=Oswald:wght@500;700&display=swap" rel="stylesheet">
<style>
  :root {
    --red: #ec1f27;
    --blue: #0355a3;
    --navy: #1f3a6e;
    --white: #ffffff;
    --page: #e6e6e6;
  }
  * { margin: 0; padding: 0; box-sizing: border-box; }
  html, body { width: 1200px; height: 1139px; overflow: hidden; background: var(--page); }
  .flyer {
    position: absolute; left: 223px; top: 15px;
    width: 754px; height: 1108px;
    background: var(--white); overflow: hidden;
    font-family: "Bebas Neue", "Oswald", sans-serif;
  }
  .flyer-shapes { position: absolute; inset: 0; }
  .abs { position: absolute; white-space: nowrap; }

  .brand { left: 34px; top: 60px; color: var(--red); font-family: "Oswald", sans-serif; font-weight: 700; line-height: 1; }
  .brand-name { font-size: 52px; letter-spacing: 1px; display: block; }
  .brand-sub { font-size: 13px; letter-spacing: 1.5px; display: block; margin-top: 4px; }

  .kicker { left: 54px; top: 268px; font-family: "Kaushan Script", cursive; font-size: 50px; line-height: 1.2; color: var(--white); transform: rotate(-6deg); }
  .headline { left: 40px; top: 360px; font-size: 124px; font-weight: 400; line-height: .9; transform: rotate(-5deg); transform-origin: left bottom; letter-spacing: 0; }
  .headline .summer { color: var(--white); }
  .headline .camp { color: var(--red); }
  .year { left: 636px; top: 306px; font-size: 54px; line-height: 1; color: var(--white); writing-mode: vertical-rl; letter-spacing: 2px; }
  .audience { left: 418px; top: 468px; font-family: "Kaushan Script", cursive; font-size: 20px; color: var(--white); transform: rotate(-8deg); }

  .weeks { left: 76px; top: 582px; color: var(--white); font-family: "Oswald", sans-serif; font-weight: 700; font-size: 29px; line-height: 43px; transform: rotate(-3deg); }

  .hosted { left: 393px; top: 562px; color: var(--navy); font-family: "Oswald", sans-serif; font-weight: 500; font-size: 11.5px; line-height: 27px; letter-spacing: .3px; text-transform: uppercase; }
  .partner-name { left: 600px; top: 560px; width: 130px; text-align: center; color: var(--red); font-family: "Oswald", sans-serif; font-weight: 700; font-size: 30px; }

  .hours { left: 103px; top: 778px; color: var(--red); font-family: "Oswald", sans-serif; font-weight: 500; font-size: 20px; line-height: 30px; }
  .cost-label { left: 112px; top: 872px; font-family: "Kaushan Script", cursive; font-size: 19px; color: var(--navy); }
  .prices { left: 210px; top: 870px; color: var(--navy); font-family: "Oswald", sans-serif; font-weight: 500; font-size: 20px; line-height: 32px; }

  .players { left: 452px; top: 808px; color: var(--navy); font-family: "Oswald", sans-serif; font-weight: 500; font-size: 30px; line-height: 46px; }
  .players .ages { display: block; }
  .age-badge { left: 571px; top: 788px; width: 126px; height: 126px; border-radius: 50%; background: var(--navy); color: var(--white); font-size: 40px; display: flex; align-items: center; justify-content: center; font-family: "Oswald", sans-serif; font-weight: 700; }

  .gear-photo { position: absolute; left: 0; top: 900px; width: 181px; height: 208px; background: radial-gradient(circle at 60% 45%, #e8ec3a 0 34%, #f4f4f0 35% 60%, #9a5a3a 100%); }

  .register { left: 194px; top: 978px; font-family: "Kaushan Script", cursive; font-size: 27px; line-height: 34px; color: var(--red); transform: rotate(-8deg); }
  .label-script { font-family: "Kaushan Script", cursive; font-size: 16px; line-height: 24px; color: var(--navy); }
  .info-line { color: #1e1e1e; font-family: "Oswald", sans-serif; font-weight: 500; font-size: 14px; line-height: 23px; }
  .location { left: 350px; top: 982px; }
  .contact { left: 551px; top: 978px; }
</style>
</head>
<body>
<main class="flyer">
  <svg class="flyer-shapes" width="754" height="1108" viewBox="0 0 754 1108">
    <defs>
      <linearGradient id="fieldTone" x1="0" y1="0" x2="0" y2="1">
        <stop offset="0" stop-color="#7f8f98"/>
        <stop offset=".45" stop-color="#9a8f6a"/>
        <stop offset="1" stop-color="#d9b57a"/>
      </linearGradient>
    </defs>
    <polygon points="298,0 754,0 754,527 0,527 0,208 225,192" fill="url(#fieldTone)" role="img" aria-label="Photo of a young player sliding into base on a sunny ballfield"/>
    <polygon points="0,527 754,527 559,536 0,560" fill="#ffffff"/>
    <polygon points="0,365 630,295 559,536 0,511" fill="var(--navy)"/>
    <polygon points="0,468 408,433 322,738 0,738" fill="var(--red)"/>
    <line x1="0" y1="549" x2="396" y2="506" stroke="#fff" stroke-width="1.5" stroke-dasharray="8 6"/>
    <line x1="323" y1="739" x2="754" y2="686" stroke="#9a9a9a" stroke-width="1.5" stroke-dasharray="6 5"/>
    <circle cx="665" cy="640" r="22" fill="#7cb342"/>
    <g transform="translate(80,802)" fill="none" stroke="var(--red)" stroke-width="3">
      <circle cx="0" cy="4" r="12"/><line x1="0" y1="4" x2="0" y2="-3"/><line x1="-4" y1="-12" x2="4" y2="-12"/>
    </g>
    <circle cx="180" cy="887" r="15" fill="var(--navy)"/>
    <text x="180" y="894" text-anchor="middle" fill="#fff" font-family="Oswald, sans-serif" font-weight="700" font-size="19">$</text>
    <g fill="var(--navy)">
      <circle cx="412" cy="818" r="5"/><path d="M405 826h14l-2 14h-2v12h-6v-12h-2z"/>
      <circle cx="430" cy="818" r="5"/><rect x="424" y="826" width="12" height="26" rx="2"/>
    </g>
    <path d="M335 978a7 7 0 0 1 7 7c0 6-7 13-7 13s-7-7-7-13a7 7 0 0 1 7-7z" fill="var(--navy)"/>
    <circle cx="335" cy="985" r="2.5" fill="#fff"/>
    <rect x="532" y="974" width="12" height="20" rx="2" fill="none" stroke="var(--navy)" stroke-width="2.5"/>
    <line x1="538" y1="968" x2="538" y2="974" stroke="var(--navy)" stroke-width="2.5"/>
  </svg>

  <div class="abs brand"><span class="brand-name">KESTREL</span><span class="brand-sub">BASEBALL &amp; SOFTBALL</span></div>

  <div class="abs kicker">softball</div>
  <h1 class="abs headline"><span class="summer">SUMMER</span><span class="camp">CAMP</span></h1>
  <div class="abs year">2017</div>
  <div class="abs audience">for boys and girls</div>

  <p class="abs weeks">WEEKS OF<br>JULY 10TH - 14TH<br>JULY 17TH - 21ST.</p>

  <p class="abs hosted">Hosted by "Kestrel Baseball"<br>Affiliated with the Harbor Comets<br>Travel Baseball &amp; Softball Club and<br>the Maple Ridge Youth League</p>
  <div class="abs partner-name">COMETS</div>

  <p class="abs hours">FULL DAY = 9:30AM - 2:30PM<br>HALF DAY = 9:30AM - 11:30AM</p>
  <div class="abs cost-label">Cost:</div>
  <p class="abs prices">$295 / FULL DAY<br>$195/ HALF DAY</p>

  <p class="abs players">PLAYERS<span class="ages">AGES</span></p>
  <div class="abs age-badge">5 - 11</div>

  <div class="gear-photo" role="img" aria-label="Photo of a yellow softball resting in a leather glove with bats"></div>
  <div class="abs register">Register<br>&nbsp;today!</div>

  <div class="abs location"><div class="label-script">Camp Location:</div><p class="info-line">CAMP LOCATION MRYL,<br>ROUTE 9C BIRCH HOLLOW.</p></div>
  <div class="abs contact"><div class="label-script">Contact:</div><p class="info-line">PHONE 555-240-7813, EMAIL<br>INFO@KESTRELBALL.EXAMPLE</p></div>
</main>
</body>
</html>
```